we can communicate on this, but i want to follow the approach we took on Pellew|Marsh & Quinlan but i feel the card front needs the black background and the platinum and gold logo. The back? I am open. we can use the same info from PM&Q. Velmont Arc is an enhanced equity investment fund - basically a very exclusive boutique hedge fund that uses only stock options. very advanced things. hope you are interested

Contact Information for Business Card

Dr. Lewis T. Brennick, CFA
Scientifique de fusée financière
701.555.0143
LTBquant47@mailvantor.com

4718 Willow Creek Bend W.
West Fargo, ND 58078

No web site

Colors

Designer to choose colors to be used in the design.

Requirements
Nice to have
• I tend to prefer the most visible applications of the logo to include logo and name, the logo version with a black background and the gold and platinum components separated by the black. I see this working well for a single side (logo and name - this is card front to me).
• I am fairly open to other treatments on the reverse side with the data. To me, it makes sense to have a different color rendition of the logo on the reverse and it may be a muted black tone on tone or an oversized portion that would have spot UV. Or, the reverse may play with colors and layout
Should not have
• Other colors = no no
• Decorative font

```html
<!DOCTYPE html>
<html lang="fr">
<head>
<meta charset="utf-8">
<title>Velmont Arc – Business Card</title>
<link rel="stylesheet" href="https://fonts.googleapis.com/css2?family=Montserrat:wght@600&family=Roboto:wght@400;700&display=swap">
<style>
  :root {
    --backdrop: #1b1b1c;
    --card: #1f2022;
    --gold: #c9a53a;
    --platinum: #d8d8da;
    --white: #ffffff;
    --rule: #9a9a9c;
  }
  html, body {
    margin: 0;
    width: 1200px;
    height: 800px;
    overflow: hidden;
    background: var(--backdrop);
  }
  .canvas {
    width: 1200px;
    height: 800px;
    display: flex;
    align-items: center;
    justify-content: center;
    gap: 50px;
  }
  .card {
    position: relative;
    width: 525px;
    height: 300px;
    background: var(--card);
    box-shadow: 0 10px 30px rgba(0,0,0,.45);
    overflow: hidden;
  }
  /* Front */
  .front-mark {
    position: absolute;
    left: 50%;
    top: 62px;
    width: 92px;
    height: 92px;
    margin-left: -46px;
    border-radius: 50%;
    background: var(--gold);
  }
  .front-name {
    position: absolute;
    left: 0; right: 0;
    top: 178px;
    text-align: center;
    font: 600 34px/1 "Montserrat", sans-serif;
    letter-spacing: 2px;
    color: var(--platinum);
    text-transform: uppercase;
  }
  /* Back */
  .back-mark {
    position: absolute;
    left: 375px;
    top: 28px;
    width: 62px;
    height: 62px;
    border-radius: 50%;
    background: var(--gold);
  }
  .back-name {
    position: absolute;
    right: 34px;
    top: 104px;
    width: 220px;
    text-align: center;
    font: 600 25px/1 "Montserrat", sans-serif;
    letter-spacing: 1px;
    color: var(--white);
    text-transform: uppercase;
  }
  .holder {
    position: absolute;
    left: 30px;
    top: 156px;
    font-family: "Roboto", sans-serif;
  }
  .holder-name {
    font-weight: 700;
    font-size: 17px;
    color: var(--gold);
  }
  .holder-name .credential { font-size: 10px; vertical-align: 5px; }
  .holder-title {
    margin-top: 3px;
    font-size: 11px;
    color: var(--white);
  }
  .rule {
    position: absolute;
    left: 30px; right: 30px;
    top: 200px;
    height: 1px;
    background: var(--rule);
  }
  .contact {
    position: absolute;
    left: 30px;
    top: 212px;
    margin: 0; padding: 0;
    list-style: none;
    font: 400 12px/1.5 "Roboto", sans-serif;
    color: var(--white);
  }
  .contact li { display: flex; align-items: center; gap: 8px; }
  .contact svg { width: 10px; height: 10px; fill: var(--gold); }
  .address {
    position: absolute;
    right: 30px;
    top: 210px;
    text-align: right;
    font: 400 12px/1.45 "Roboto", sans-serif;
    color: var(--white);
    font-style: normal;
  }
  .footer-band {
    position: absolute;
    left: 0; bottom: 0;
    width: 525px; height: 46px;
  }
</style>
</head>
<body>
<main class="canvas">

  <section class="card card-front" aria-label="Card front">
    <div class="front-mark"></div>
    <div class="front-name">Velmont Arc</div>
  </section>

  <section class="card card-back" aria-label="Card back">
    <div class="back-mark"></div>
    <div class="back-name">Velmont Arc</div>

    <div class="holder">
      <div class="holder-name">Dr. Lewis T. Brennick, <span class="credential">CFA</span></div>
      <div class="holder-title">Scientifique des Fusées Financières</div>
    </div>

    <div class="rule"></div>

    <ul class="contact">
      <li>
        <svg viewBox="0 0 10 10" aria-hidden="true"><path d="M3 0h4a1 1 0 0 1 1 1v8a1 1 0 0 1-1 1H3a1 1 0 0 1-1-1V1a1 1 0 0 1 1-1zm0 1.5v6h4v-6z"/></svg>
        701.555.0143
      </li>
      <li>
        <svg viewBox="0 0 10 10" aria-hidden="true"><path d="M0 2h10v6H0zM1 3l4 3 4-3"/></svg>
        LTBquant47@mailvantor.com
      </li>
    </ul>

    <address class="address">
      4718 Willow Creek Bend W.<br>
      West Fargo, ND 58078
    </address>

    <svg class="footer-band" viewBox="0 0 525 46" aria-hidden="true">
      <path d="M0 40 L255 40 Q268 40 276 30 L290 16 Q296 10 306 10 L525 10 L525 14 L306 14 Q298 14 292 20 L278 34 Q270 44 255 44 L0 44 Z" fill="var(--platinum)"/>
      <path d="M0 44 L255 44 Q270 44 278 34 L292 20 Q298 14 306 14 L525 14 L525 46 L0 46 Z" fill="var(--gold)"/>
    </svg>
  </section>

</main>
</body>
</html>
```